Velk Partners Building Business Cards

We need a business card that reflects our business as "Solar Experts" in San Diego. Browse our website www.velkpartners.example our License needs to be displayed as "CSLB# 3867140" our phone number is (619) 555-0187

Save thousands on your electric bills and increase the value of your home while helping to protect the environment. Our solar installation experts will help you design the system that's right for you, using only the highest quality equipment that will look great and give you ideal performance. Our goal is to make you energy independent, and get your electric bill to 0.

Paul Osterby
(619) 555-0187
paul@velkpartners.example

Target Market(s)

Home owners in san diego looking for solar

Industry/Entity Type

Solar Energy

Contact Information for Business Card

Paul Osterby
(619) 555-0187
paul@velkpartners.example

Font styles to use
Other font styles liked:
• Use our logo font

Requirements
Must have
• License needs to be displayed as "CSLB# 3867140" our phone number is (619) 555-0187
Nice to have
• Real images of rooftop home solar in san diego
Should not have
• our business address

```html
<!DOCTYPE html>
<html lang="en">
<head>
<meta charset="utf-8">
<title>Velk Partners Building – Business Cards</title>
<link rel="stylesheet" href="https://fonts.googleapis.com/css2?family=Open+Sans:wght@400;600;700&display=swap">
<style>
  :root {
    --navy: #1f3d7a;
    --gold: #f7ae00;
    --white: #ffffff;
    --backdrop: #e9e6e3;
    --card-shadow: 0 6px 18px rgba(0, 0, 0, 0.22);
  }
  * { margin: 0; padding: 0; box-sizing: border-box; }
  html, body {
    width: 1200px;
    height: 900px;
    overflow: hidden;
    background: var(--backdrop);
    font-family: "Open Sans", Arial, sans-serif;
  }
  .stage { position: relative; width: 1200px; height: 900px; }

  .card {
    position: absolute;
    overflow: hidden;
    box-shadow: var(--card-shadow);
  }

  /* Front card */
  .card-front {
    left: 78px; top: 34px;
    width: 588px; height: 363px;
    background: var(--white);
  }
  .card-front .bands {
    position: absolute; left: 0; top: 0;
    width: 588px; height: 363px;
  }
  .brand-name {
    position: absolute;
    left: 0; right: 0; top: 92px;
    text-align: center;
    font-weight: 700;
    font-size: 42px;
    letter-spacing: -0.5px;
    color: var(--navy);
  }
  .contact {
    position: absolute;
    top: 272px;
    color: var(--white);
  }
  .contact-person {
    right: 316px;
    text-align: right;
  }
  .person-name {
    font-weight: 600;
    font-size: 18px;
    line-height: 24px;
  }
  .license {
    font-size: 13.5px;
    line-height: 22px;
  }
  .license strong { font-weight: 600; }
  .contact-lines {
    left: 292px;
    font-size: 14px;
  }
  .contact-line {
    display: flex;
    align-items: center;
    gap: 11px;
    height: 24px;
  }
  .contact-line svg { width: 14px; height: 14px; fill: var(--white); }

  /* Back card */
  .card-back {
    left: 388px; top: 505px;
    width: 567px; height: 352px;
    background: var(--navy);
  }
  .card-back .brand-name {
    top: 148px;
    font-size: 40px;
    color: var(--white);
  }
</style>
</head>
<body>
<main class="stage">

  <section class="card card-front" aria-label="Business card front">
    <svg class="bands" viewBox="0 0 588 363" aria-hidden="true">
      <polygon points="0,199 402,199 384,226 0,226" fill="var(--gold)"/>
      <polygon points="0,229 384,229 414,192 588,192 588,363 0,363" fill="var(--navy)"/>
    </svg>

    <div class="brand-name">Velk Partners Building</div>

    <div class="contact contact-person">
      <div class="person-name">Paul Osterby</div>
      <div class="license"><strong>License:</strong> CSLB# 3867140</div>
    </div>

    <div class="contact contact-lines">
      <div class="contact-line">
        <svg viewBox="0 0 24 24" aria-hidden="true"><path d="M6.6 10.8a15.1 15.1 0 0 0 6.6 6.6l2.2-2.2c.3-.3.7-.4 1-.2 1.1.4 2.3.6 3.6.6.6 0 1 .4 1 1V20c0 .6-.4 1-1 1A17 17 0 0 1 3 4c0-.6.4-1 1-1h3.5c.6 0 1 .4 1 1 0 1.3.2 2.5.6 3.6.1.3 0 .7-.2 1z"/></svg>
        <span>(619) 555-0187</span>
      </div>
      <div class="contact-line">
        <svg viewBox="0 0 24 24" aria-hidden="true"><path d="M2 5h20v14H2z M3.5 6.5 12 13l8.5-6.5" fill="none" stroke="var(--white)" stroke-width="2"/></svg>
        <span>paul@velkpartners.example</span>
      </div>
    </div>
  </section>

  <section class="card card-back" aria-label="Business card back">
    <div class="brand-name">Velk Partners Building</div>
  </section>

</main>
</body>
</html>
```